Corvel Capital LLC

Need Professional Business cards for New Investment Fund

Target Market(s)

High Quality investors

Industry/Entity Type

Financial

Contact Information for Business Card

Phone Number +1 555 284 6190
Name Lukas Varenko
Title Fund Manager
email lv@FundCorvel.com
Website www.FundCorvel.com

Colors

Designer to choose colors to be used in the design.

Requirements
Must have
• Must have our Logo and all of the above. Must be made so lettering and loge can be raised

```html
<!DOCTYPE html>
<html lang="en">
<head>
<meta charset="utf-8">
<title>Quarnel – Business Card</title>
<link rel="stylesheet" href="https://fonts.googleapis.com/css2?family=Roboto:wght@400;500;700&display=swap">
<style>
  :root {
    --page-bg: #2a2a2a;
    --card-bg: #1b1b1b;
    --accent: #8dc21f;
    --ink-light: #e4e4e4;
    --ink-muted: #d0d0d0;
    --emboss: #4a4a4a;
  }
  * { margin: 0; padding: 0; box-sizing: border-box; }
  html, body {
    width: 1200px; height: 1138px; overflow: hidden;
    background: var(--page-bg);
    font-family: "Roboto", Arial, sans-serif;
  }
  .canvas { position: relative; width: 1200px; height: 1138px; }
  .card {
    position: absolute;
    width: 620px; height: 374px;
    background: var(--card-bg);
    border-radius: 16px;
  }
  .card--front { left: 274px; top: 186px; }
  .card--back { left: 276px; top: 608px; }

  .wordmark {
    position: absolute;
    font-weight: 500;
    letter-spacing: 1px;
    line-height: 1;
    white-space: nowrap;
  }
  .card--front .wordmark {
    left: 0; right: 0; top: 160px;
    text-align: center;
    font-size: 66px;
    color: var(--emboss);
  }
  .card--back .wordmark {
    left: 58px; top: 200px;
    font-size: 46px;
    color: var(--ink-light);
  }

  .contact-block { position: absolute; left: 346px; top: 110px; }
  .person-name {
    font-size: 24px; font-weight: 700;
    color: var(--accent);
    line-height: 1.1;
  }
  .person-title {
    font-size: 16px; color: var(--ink-muted);
    margin-top: 6px;
  }
  .contact-list { list-style: none; margin-top: 30px; }
  .contact-list li {
    display: flex; align-items: center;
    font-size: 16px; color: var(--ink-light);
    height: 24px;
    white-space: nowrap;
  }
  .contact-list svg { width: 14px; height: 14px; margin-right: 18px; fill: var(--accent); flex: none; }
</style>
</head>
<body>
<main class="canvas">
  <section class="card card--front" aria-label="Card front">
    <div class="wordmark">QUARNEL</div>
  </section>

  <section class="card card--back" aria-label="Card back">
    <div class="wordmark">QUARNEL</div>
    <div class="contact-block">
      <p class="person-name">Lukas Varenko</p>
      <p class="person-title">Fund Manager</p>
      <ul class="contact-list">
        <li>
          <svg viewBox="0 0 16 16" aria-hidden="true"><path d="M1 5c0-2 3-3 7-3s7 1 7 3v1h-3V4.5H4V6H1z"/><path d="M3 7h10l1 7H2z"/></svg>
          +1 555 284 6190
        </li>
        <li>
          <svg viewBox="0 0 16 16" aria-hidden="true"><path d="M1 3h14v10H1z M2.5 4.5 8 9l5.5-4.5" fill="none" stroke="#8dc21f" stroke-width="1.6"/></svg>
          lv@FundCorvel.com
        </li>
        <li>
          <svg viewBox="0 0 16 16" aria-hidden="true"><g fill="none" stroke="#8dc21f" stroke-width="1.4"><circle cx="8" cy="8" r="6.5"/><ellipse cx="8" cy="8" rx="3" ry="6.5"/><path d="M1.5 8h13M2.5 4.8h11M2.5 11.2h11"/></g></svg>
          www.FundCorvel.com
        </li>
      </ul>
    </div>
  </section>
</main>
</body>
</html>
```